Business card for Sports Apparel business

DOUBLE SIDED DESIGN
We need business cards for a new sports apparel business. We are developing a protective headband for soccer initially.
Torvalle is focused on designing and developing head protection products to reduce the likelihood of concussion when playing sports. Exploring and understanding medical insights, material science research, current and former players experiences and governing bodies guidelines has allowed Torvalle to develop the safety, style, form and function requirements of a suitable product to bring to market.
Target Market(s)
Mums buying kits for the sons and daughters. Amateur footballers.
Industry/Entity Type
Sporting Good
Contact Information for Business Card
Martin Ashworth - CEO
Mobile: +44 7431589027
Email: martin@torvalle.co.uk
Tel: 0208 5519372
Helena Pargeter - COO
Mob: +44 7385 640117
Email: helena@torvalle.co.uk
Tel: 0208 5519372
Duncan Farrow - CCO
Mob: +44 7564 293081
Email: duncan@torvalle.co.uk
Tel: 0208 5519372
Look and feel
Each slider illustrates characteristics of the customer's brand and the style your logo design should communicate.

```html
<!DOCTYPE html>
<html lang="en">
<head>
<meta charset="utf-8">
<title>Torvalle business card</title>
<link rel="stylesheet" href="https://fonts.googleapis.com/css2?family=Montserrat:wght@400;500;600&display=swap">
<style>
  :root {
    --brand-blue: #0f5f9c;
    --ink-grey: #5f6063;
    --ink-dark: #3a3b3d;
    --card-white: #ffffff;
    --backdrop: #e6e6e4;
  }
  * { box-sizing: border-box; margin: 0; padding: 0; }
  html, body {
    width: 1200px; height: 930px; overflow: hidden;
    background: var(--backdrop);
    font-family: "Montserrat", sans-serif;
  }
  .canvas { position: relative; width: 1200px; height: 930px; }
  .card {
    position: absolute;
    width: 560px; height: 320px;
    background: var(--card-white);
    border-radius: 22px;
    overflow: hidden;
    box-shadow: 0 10px 28px rgba(0,0,0,0.18);
  }
  /* Front */
  .card--front { left: 110px; top: 110px; border-bottom: 6px solid var(--brand-blue); }
  .brand-name {
    position: absolute; left: 0; right: 0; top: 112px;
    text-align: center;
    font-size: 60px; font-weight: 600; letter-spacing: 2px;
    color: var(--ink-grey);
    text-transform: uppercase;
  }
  .front-url {
    position: absolute; left: 0; right: 0; bottom: 28px;
    text-align: center; font-size: 14px; font-weight: 500;
    letter-spacing: 1.5px; color: var(--ink-dark);
  }
  .front-url .accent, .contact-url .accent { color: var(--brand-blue); font-weight: 600; }
  /* Back */
  .card--back { left: 530px; top: 500px; }
  .side-band {
    position: absolute; left: 0; top: 0; bottom: 0; width: 200px;
    background: var(--brand-blue);
  }
  .side-band__name {
    position: absolute; left: 100px; top: 160px;
    transform: translate(-50%, -50%) rotate(-90deg);
    font-size: 44px; font-weight: 600; letter-spacing: 2px;
    color: var(--card-white); text-transform: uppercase; white-space: nowrap;
  }
  .details { position: absolute; left: 250px; top: 62px; }
  .details__name {
    font-size: 24px; font-weight: 600; color: var(--brand-blue);
    text-transform: uppercase; letter-spacing: 0.5px;
  }
  .details__role { font-size: 16px; color: var(--ink-grey); margin-top: 2px; }
  .details__rule { width: 26px; height: 2px; background: var(--brand-blue); margin: 14px 0 16px; }
  .contact-list { list-style: none; }
  .contact-list li {
    display: flex; align-items: center; gap: 10px;
    font-size: 15px; color: var(--ink-dark); margin-bottom: 7px;
  }
  .contact-icon { width: 18px; height: 18px; flex: none; }
</style>
</head>
<body>
<main class="canvas">
  <section class="card card--front" aria-label="Card front">
    <div class="brand-name">Torvalle</div>
    <div class="front-url">www.<span class="accent">torvalle</span>.co.uk</div>
  </section>

  <section class="card card--back" aria-label="Card back">
    <div class="side-band"><div class="side-band__name">Torvalle</div></div>
    <div class="details">
      <div class="details__name">Helena Pargeter</div>
      <div class="details__role">COO</div>
      <div class="details__rule"></div>
      <ul class="contact-list">
        <li>
          <svg class="contact-icon" viewBox="0 0 18 18" aria-hidden="true"><rect width="18" height="18" rx="4" fill="#0f5f9c"/><path d="M5.5 4.5l2 .2.8 2.2-1.2 1a6 6 0 0 0 3 3l1-1.2 2.2.8.2 2c-4.5.8-8.8-3.5-8-8z" fill="#fff"/></svg>
          0208 5519372
        </li>
        <li>
          <svg class="contact-icon" viewBox="0 0 18 18" aria-hidden="true"><rect width="18" height="18" rx="4" fill="#0f5f9c"/><rect x="6" y="3.5" width="6" height="11" rx="1.2" fill="none" stroke="#fff" stroke-width="1.4"/><circle cx="9" cy="12.3" r=".8" fill="#fff"/></svg>
          +44 7385 640117
        </li>
        <li>
          <svg class="contact-icon" viewBox="0 0 18 18" aria-hidden="true"><rect width="18" height="18" rx="4" fill="#0f5f9c"/><rect x="4" y="5.5" width="10" height="7" fill="none" stroke="#fff" stroke-width="1.3"/><path d="M4 5.5l5 4 5-4" fill="none" stroke="#fff" stroke-width="1.3"/></svg>
          helena@torvalle.co.uk
        </li>
        <li class="contact-url">
          <svg class="contact-icon" viewBox="0 0 18 18" aria-hidden="true"><rect width="18" height="18" rx="4" fill="#0f5f9c"/><circle cx="9" cy="9" r="5" fill="none" stroke="#fff" stroke-width="1.2"/><ellipse cx="9" cy="9" rx="2.2" ry="5" fill="none" stroke="#fff" stroke-width="1"/><path d="M4 9h10" stroke="#fff" stroke-width="1"/></svg>
          <span>www.<span class="accent">torvalle</span>.co.uk</span>
        </li>
      </ul>
    </div>
  </section>
</main>
</body>
</html>
```